New Business Card Design Project LORVANTI-Italy

we are LORVANTI-Italy
our company in the market for 3 years we are luxury cosmetic company and its about time for a facelift :)
i will like to have elegant luxurious and unique business card
that will give the person that get it a unique, luxurious and elegant impression
I'm VERY OPEN FOR NEW IDEAS , even duo i add a few files of things that i see on line and i like them

i add my logo as well
my website is LORVANTI.COM
(if you would like to see the main style that we have)

Target Market(s)

adult that have money :)

Industry/Entity Type

Business

Contact Information for Business Card

Name - Dario Lorvanti
Position - CEO and CO Founder
address - 4817 E Halvern
telephone - 555-384-1926
email - dario@lorvanti.com
fax - 555-384-1926
website - LORVANTI.COM

Colors
000000
959595
fbee3e
ffffff

Requirements
Must have
• big logo in GOLD color
• elegant look
• impressive
Nice to have
• not must but maybe classy pattern background
• not must but maybe emblem
• maybe clear plastic business card
Should not have
• colors
• images

```html
<!DOCTYPE html>
<html lang="en">
<head>
<meta charset="utf-8">
<title>LORVANTI-Italy — Business Card</title>
<link href="https://fonts.googleapis.com/css2?family=Tinos:wght@400;700&display=swap" rel="stylesheet">
<style>
  :root {
    --backdrop: #1b1b1b;
    --card: #141414;
    --gold: #d4a93a;
    --white: #f4f4f4;
    --grey: #959595;
    --emboss: #2a2a2a;
  }
  * { margin: 0; padding: 0; box-sizing: border-box; }
  html, body {
    width: 1200px;
    height: 833px;
    overflow: hidden;
    background: var(--backdrop);
    font-family: "Tinos", "Times New Roman", serif;
  }
  .stage {
    position: relative;
    width: 1200px;
    height: 833px;
  }
  .card {
    position: absolute;
    top: 268px;
    width: 520px;
    height: 297px;
    background: var(--card);
    box-shadow: 0 0 0 1px #222;
  }
  .card--front { left: 50px; }
  .card--back { left: 630px; }

  /* Front */
  .brand {
    position: absolute;
    inset: 0;
    display: flex;
    flex-direction: column;
    align-items: center;
    justify-content: center;
    gap: 18px;
  }
  .brand__dot {
    width: 62px;
    height: 62px;
    border-radius: 50%;
    background: var(--gold);
  }
  .brand__name {
    color: var(--gold);
    font-size: 40px;
    font-weight: 400;
    letter-spacing: 2px;
  }

  /* Back */
  .contact {
    position: absolute;
    left: 64px;
    top: 52px;
    color: var(--white);
    font-size: 15px;
    line-height: 1.3;
  }
  .contact__name {
    color: var(--gold);
    font-size: 21px;
    font-weight: 700;
  }
  .contact__role { margin-bottom: 10px; }
  .contact__company {
    color: var(--gold);
    font-weight: 700;
    font-size: 16px;
  }
  .contact__address { margin-bottom: 10px; }
  .contact__line {
    display: flex;
    align-items: center;
    gap: 8px;
  }
  .contact__line svg {
    width: 12px;
    height: 12px;
    flex: none;
    fill: var(--gold);
  }
  .seal {
    position: absolute;
    right: 34px;
    bottom: 34px;
    width: 140px;
    height: 140px;
    border-radius: 50%;
    border: 2px solid var(--emboss);
  }
</style>
</head>
<body>
<main class="stage">
  <section class="card card--front">
    <div class="brand">
      <div class="brand__dot"></div>
      <div class="brand__name">LORVANTI</div>
    </div>
  </section>

  <section class="card card--back">
    <div class="contact">
      <div class="contact__name">Dario Lorvanti</div>
      <div class="contact__role">CEO and CO Founder</div>
      <div class="contact__company">LORVANTI-Italy</div>
      <div class="contact__address">4817 E Halvern</div>
      <div class="contact__line">
        <svg viewBox="0 0 12 12" aria-hidden="true"><path d="M2.5 0.8l2 2.2-1 1.3c.7 1.5 1.8 2.6 3.3 3.3l1.3-1 2.2 2-1.2 2C5.8 10.4 1.6 6.2 0.8 2z"/></svg>
        <span>555-384-1926</span>
      </div>
      <div class="contact__line">
        <svg viewBox="0 0 12 12" aria-hidden="true"><path d="M3 1h5v3H3zM1 5h10v6H1zM3 8h6v1H3z"/></svg>
        <span>555-384-1926</span>
      </div>
      <div class="contact__line">
        <svg viewBox="0 0 12 12" aria-hidden="true"><path d="M0.5 2.5h11v7h-11zM1.5 3.5L6 7l4.5-3.5" stroke="#141414" stroke-width="0.8"/></svg>
        <span>dario@lorvanti.com</span>
      </div>
      <div class="contact__line">
        <svg viewBox="0 0 12 12" aria-hidden="true"><circle cx="6" cy="6" r="5.3"/><path d="M0.7 6h10.6M6 0.7v10.6M2 3.3h8M2 8.7h8" stroke="#141414" stroke-width="0.7" fill="none"/><ellipse cx="6" cy="6" rx="2.3" ry="5.3" stroke="#141414" stroke-width="0.7" fill="none"/></svg>
        <span>LORVANTI.COM</span>
      </div>
    </div>
    <div class="seal" role="img" aria-label="Blind-embossed brand emblem"></div>
  </section>
</main>
</body>
</html>
```